Business Card Design

Bowen therapy is a gentle therapy where moves are made(using your hands) over muscles or joint areas create myofascial release enabling the body to rebalance itself.

Its relaxing and have heal a variety of aliments . n contrast to other hands-on modalities, where the practitioner imposes correction on the client through manipulation, Bowen Technique facilitates the body in healing itself, with minimal intervention. Because of the subtle nature of Bowen Technique, and the body's continuing response to it over several days thereafter, other forms of manipulative therapy are discouraged for up to five days after a session, as they may interfere with the efficacy of the work.

Its an energy healing work using hands.
Its relaxing but professional.
I'm think of using blues, no greens or yellows. Some wave lines .

Target Market(s)

Anybody-

Industry/Entity Type

Business

Contact Information for Business Card

Lorna's Calm Therapy,Lorna Pettigrew, Bowen Therapist,Cert IV Kinelia
Singleton, North Arm Cove, Maitland, 0491 375068,Gentle therapy restoring body balance.

Requirements
Must have
• Back needs a appointment table
with this wording :
Bowen Therapy is a subtle gentle bodywork therapy where a series of moves are made over muscles that can be used to address a wide range of conditions. It is suitable for skeletal, joint and muscle problems as well as for babies and children
Date Time.

If you are unable to keep your appointment, please contact us as soon as possible.

0491375068 lornacalm@mailfern.net
Should not have
• Dont like times new roman and handwritten script font.

```html
<!DOCTYPE html>
<html lang="en">
<head>
<meta charset="utf-8">
<title>Lorna's Calm Therapy — Business Card</title>
<link rel="stylesheet" href="https://fonts.googleapis.com/css2?family=Arimo:wght@400;700&family=Exo+2:wght@400;500;600&display=swap">
<style>
  :root {
    --page-bg: #e4e6e9;
    --card-white: #ffffff;
    --card-mist: #dde6ef;
    --ink: #22384f;
    --ink-soft: #3d5a78;
    --band-dark: #1f3b57;
    --ribbon: #5b86ad;
    --ribbon-fold: #3c6489;
    --wave: #7fa7cc;
    --wave-soft: #b9d0e6;
    --on-dark: #ffffff;
    --metal-light: #a9c4de;
    --metal-dark: #142a40;
    --rule: #9fb6cc;
  }
  * { margin: 0; padding: 0; box-sizing: border-box; }
  html, body { width: 1200px; height: 869px; overflow: hidden; }
  body { background: var(--page-bg); position: relative; font-family: "Arimo", Arial, sans-serif; }

  .card {
    position: absolute;
    width: 600px;
    height: 340px;
    overflow: hidden;
    box-shadow: 0 6px 18px rgba(0,0,0,0.18);
  }
  .card-art { position: absolute; inset: 0; }

  /* Appointment side */
  .card--plain {
    left: 60px; top: 60px;
    background: linear-gradient(160deg, var(--card-white) 30%, var(--card-mist) 100%);
  }
  .card--plain .brand-name {
    position: absolute;
    left: 30px; top: 20px;
    font-size: 32px;
    font-weight: 400;
    color: var(--ink);
  }
  .about {
    position: absolute;
    left: 30px; top: 66px; width: 540px;
    font-size: 11.5px;
    line-height: 1.4;
    color: var(--ink-soft);
  }
  .appointments {
    position: absolute;
    left: 30px; top: 126px; width: 540px;
    border-collapse: collapse;
    font-size: 12px;
    color: var(--ink);
  }
  .appointments th {
    text-align: left;
    font-weight: 700;
    padding: 3px 8px;
    background: var(--wave-soft);
    border: 1px solid var(--rule);
  }
  .appointments td {
    height: 22px;
    border: 1px solid var(--rule);
  }
  .notice {
    position: absolute;
    left: 30px; top: 236px; width: 540px;
    font-size: 11.5px;
    color: var(--ink-soft);
  }
  .back-contacts {
    position: absolute;
    left: 30px; top: 258px;
    font-size: 12px;
    font-weight: 700;
    color: var(--ink);
    display: flex; gap: 28px;
  }

  /* Contact side */
  .card--contact {
    left: 540px; top: 470px;
    background: var(--band-dark);
  }
  .card--contact .brand-name {
    position: absolute;
    left: 30px; top: 30px;
    font-size: 36px;
    font-weight: 400;
    color: var(--ink);
  }
  .address {
    position: absolute;
    left: 52px; top: 124px;
    font-family: "Exo 2", Arial, sans-serif;
    font-size: 13px;
    color: var(--on-dark);
    letter-spacing: 0.3px;
  }
  .person { position: absolute; left: 404px; top: 118px; font-family: "Exo 2", Arial, sans-serif; }
  .person-name { font-size: 18px; font-weight: 600; color: var(--ink); letter-spacing: 1.2px; }
  .person-role { font-size: 10px; font-weight: 500; color: var(--ink-soft); letter-spacing: 1.5px; margin-top: 2px; }
  .person-cert { font-size: 10px; font-weight: 500; color: var(--ink-soft); letter-spacing: 1px; }

  .contact-line {
    position: absolute;
    display: flex;
    align-items: center;
    gap: 12px;
    font-family: "Exo 2", Arial, sans-serif;
    font-size: 13px;
    color: var(--on-dark);
    letter-spacing: 0.5px;
  }
  .contact-line svg { width: 24px; height: 24px; flex: none; }
  .contact-line--web { left: 30px; top: 168px; }
  .contact-line--mail { left: 30px; top: 202px; }
  .contact-line--phone { left: 400px; top: 222px; font-size: 14px; letter-spacing: 1.5px; }
  .contact-line--mobile { left: 400px; top: 256px; font-size: 14px; letter-spacing: 1.5px; }
</style>
</head>
<body>

  <section class="card card--plain" aria-label="Business card, appointment side">
    <svg class="card-art" viewBox="0 0 600 340" aria-hidden="true">
      <path d="M0 300 C120 270 220 330 340 300 S520 280 600 295" fill="none" stroke="var(--wave)" stroke-width="3"/>
      <path d="M0 318 C140 292 240 346 360 316 S530 298 600 312" fill="none" stroke="var(--wave-soft)" stroke-width="3"/>
    </svg>
    <h1 class="brand-name">Lorna's Calm Therapy</h1>
    <p class="about">Bowen Therapy is a subtle gentle bodywork therapy where a series of moves are made over muscles that can be used to address a wide range of conditions. It is suitable for skeletal, joint and muscle problems as well as for babies and children.</p>
    <table class="appointments">
      <thead><tr><th>Date</th><th>Time</th></tr></thead>
      <tbody>
        <tr><td></td><td></td></tr>
        <tr><td></td><td></td></tr>
        <tr><td></td><td></td></tr>
      </tbody>
    </table>
    <p class="notice">If you are unable to keep your appointment, please contact us as soon as possible.</p>
    <p class="back-contacts"><span>0491375068</span><span>lornacalm@mailfern.net</span></p>
  </section>

  <section class="card card--contact" aria-label="Business card, contact side">
    <svg class="card-art" viewBox="0 0 600 340" aria-hidden="true">
      <defs>
        <linearGradient id="top-panel" x1="0" y1="0" x2="1" y2="1">
          <stop offset="0" stop-color="#f6f9fc"/>
          <stop offset="1" stop-color="#d3e0ec"/>
        </linearGradient>
        <linearGradient id="metal-strip" x1="0" y1="0" x2="1" y2="0">
          <stop offset="0" stop-color="var(--metal-dark)"/>
          <stop offset="0.45" stop-color="var(--metal-light)"/>
          <stop offset="1" stop-color="var(--metal-dark)"/>
        </linearGradient>
      </defs>
      <rect x="0" y="0" width="600" height="340" fill="var(--band-dark)"/>
      <polygon class="top-panel" points="0,0 600,0 600,205 400,205 382,135 0,135" fill="url(#top-panel)"/>
      <path d="M40 72 C140 56 240 92 340 74 S520 60 600 70" fill="none" stroke="var(--wave-soft)" stroke-width="2"/>
      <rect class="metal-strip" x="0" y="292" width="600" height="48" fill="url(#metal-strip)"/>
      <path d="M0 312 C140 296 260 330 380 310 S540 300 600 308" fill="none" stroke="var(--wave)" stroke-width="2"/>
      <rect x="0" y="292" width="600" height="2" fill="#10233a"/>
      <polygon class="ribbon-fold" points="360,148 382,148 400,205 378,205" fill="var(--ribbon-fold)"/>
      <polygon class="ribbon" points="22,116 372,116 382,148 22,148" fill="var(--ribbon)"/>
      <polygon points="22,116 40,116 40,156 22,148" fill="var(--ribbon-fold)"/>
    </svg>

    <h2 class="brand-name">Lorna's Calm Therapy</h2>
    <p class="address">Singleton, North Arm Cove, Maitland</p>

    <div class="person">
      <p class="person-name">LORNA PETTIGREW</p>
      <p class="person-role">BOWEN THERAPIST</p>
      <p class="person-cert">Cert IV Kinelia</p>
    </div>

    <p class="contact-line contact-line--web">
      <svg viewBox="0 0 24 24" aria-hidden="true">
        <rect width="24" height="24" rx="3" fill="#fff"/>
        <circle cx="12" cy="12" r="7" fill="none" stroke="#1f3b57" stroke-width="1.5"/>
        <ellipse cx="12" cy="12" rx="3" ry="7" fill="none" stroke="#1f3b57" stroke-width="1.3"/>
        <line x1="5" y1="12" x2="19" y2="12" stroke="#1f3b57" stroke-width="1.3"/>
      </svg>
      www.lornacalm.net
    </p>
    <p class="contact-line contact-line--mail">
      <svg viewBox="0 0 24 24" aria-hidden="true">
        <rect width="24" height="24" rx="3" fill="#fff"/>
        <rect x="5" y="7" width="14" height="10" fill="none" stroke="#1f3b57" stroke-width="1.5"/>
        <polyline points="5,7 12,13 19,7" fill="none" stroke="#1f3b57" stroke-width="1.5"/>
      </svg>
      lornacalm@mailfern.net
    </p>
    <p class="contact-line contact-line--phone">
      <svg viewBox="0 0 24 24" aria-hidden="true">
        <rect width="24" height="24" rx="3" fill="#fff"/>
        <path d="M9 6 L11 9 L9.5 10.5 Q11 13.5 13.5 14.5 L15 13 L18 15 L16.5 18 Q9 17 6.5 8 Z" fill="#1f3b57"/>
      </svg>
      02 4917 3358
    </p>
    <p class="contact-line contact-line--mobile">
      <svg viewBox="0 0 24 24" aria-hidden="true">
        <rect width="24" height="24" rx="3" fill="#fff"/>
        <rect x="8" y="4.5" width="8" height="15" rx="1.5" fill="#1f3b57"/>
        <rect x="9.3" y="6.5" width="5.4" height="9" fill="#fff"/>
      </svg>
      0491 375068
    </p>
  </section>

</body>
</html>
```